Irrigation Business needs their business cards modernised and revamped

I would like to keep my current logo, colours and revamp the format of the card.

I would like the card to be clean yet important.

Im not sure if you include texture but i would like the named logo to be indented into the card etc.

show me something alive and free something thats clinical to the point yet has a feel of achievement. i would like people to go nice card.

Target Market(s)

high end clients, corporate, sports field manger, the guys that make the decisions

Industry/Entity Type

Business

Contact Information for Business Card

nformation to be included

Dean Harlow (Director)
0487305526
dean@kolvat.biz
www.kestonfieldworks.com

instagram logo
google logo
facebook logo

Colors

Designer to choose colors to be used in the design.

Requirements
Nice to have
• indentations a really nice feel to the card good texture

```html
<!DOCTYPE html>
<html lang="en">
<head>
<meta charset="utf-8">
<title>Keston Fieldworks – Business Card</title>
<link href="https://fonts.googleapis.com/css2?family=Roboto:wght@400;700;900&display=swap" rel="stylesheet">
<style>
  :root {
    --canvas: #e6e6e6;
    --card: #f7f7f8;
    --card-edge: #ececee;
    --navy: #2f4a8a;
    --sky: #3a8fc7;
    --ink: #2b2b2b;
    --muted: #444;
    --ghost: rgba(47, 74, 138, 0.06);
    --social: #7a8bb5;
  }
  * { margin: 0; padding: 0; box-sizing: border-box; }
  html, body {
    width: 1200px; height: 576px; overflow: hidden;
    background: var(--canvas);
    font-family: "Roboto", Arial, sans-serif;
  }
  .stage { position: relative; width: 1200px; height: 576px; }

  .card {
    position: absolute; top: 138px;
    width: 484px; height: 294px;
    background: linear-gradient(135deg, #fbfbfc 0%, var(--card) 55%, var(--card-edge) 100%);
    border-radius: 12px;
    overflow: hidden;
    box-shadow: 0 3px 8px rgba(0,0,0,0.18);
  }
  .card--front { left: 82px; }
  .card--back  { left: 602px; }

  .ghost-ring {
    position: absolute; border-radius: 50%;
    border: 14px solid var(--ghost);
  }
  .card--front .ghost-ring { width: 230px; height: 230px; left: 290px; top: 20px; }
  .card--back  .ghost-ring { width: 230px; height: 230px; left: 340px; top: 10px; }

  .mark {
    position: absolute; border-radius: 50%;
    background: var(--sky);
  }
  .card--front .mark { width: 92px; height: 92px; left: 196px; top: 56px; }
  .card--back  .mark { width: 80px; height: 80px; left: 24px; top: 32px; }

  .brand-name {
    position: absolute; color: var(--navy);
    font-weight: 900; letter-spacing: -0.3px; white-space: nowrap;
  }
  .card--front .brand-name { left: 0; width: 100%; text-align: center; top: 162px; font-size: 29px; }
  .card--back  .brand-name { left: 122px; top: 58px; font-size: 26px; }

  .social { position: absolute; display: flex; gap: 6px; }
  .social span { width: 17px; height: 17px; border-radius: 50%; background: var(--social); }
  .card--front .social { left: 214px; top: 264px; }
  .card--back  .social { left: 26px; top: 242px; gap: 7px; }
  .card--back  .social span { width: 20px; height: 20px; }

  .rule {
    position: absolute; top: 272px; height: 2px; width: 120px;
    background: linear-gradient(90deg, transparent, var(--navy));
  }
  .rule--left { left: 78px; }
  .rule--right { left: 286px; background: linear-gradient(90deg, var(--navy), transparent); }

  .person { position: absolute; left: 28px; top: 172px; }
  .person__name { font-size: 19px; font-weight: 700; color: var(--navy); }
  .person__role { font-size: 11.5px; color: var(--muted); margin-top: 4px; }

  .contact { position: absolute; left: 248px; top: 174px; list-style: none; }
  .contact li {
    display: flex; align-items: center; gap: 10px;
    font-size: 12.5px; color: var(--ink); height: 17px;
  }
  .contact svg { width: 10px; height: 10px; fill: var(--navy); flex: none; }

  .strip {
    position: absolute; left: 0; bottom: 0; width: 100%; height: 14px;
    background: var(--sky);
  }
  .band {
    position: absolute; right: 0; bottom: 0; width: 282px; height: 34px;
    background: var(--navy);
    clip-path: polygon(18px 0, 100% 0, 100% 100%, 0 100%);
    color: #fff; font-size: 12.5px;
    display: flex; align-items: center; padding-left: 38px;
  }
</style>
</head>
<body>
<main class="stage">

  <section class="card card--front">
    <div class="ghost-ring"></div>
    <div class="mark"></div>
    <div class="brand-name">KESTON FIELDWORKS</div>
    <div class="rule rule--left"></div>
    <div class="social" aria-label="Social profiles"><span></span><span></span><span></span></div>
    <div class="rule rule--right"></div>
  </section>

  <section class="card card--back">
    <div class="ghost-ring"></div>
    <div class="mark"></div>
    <div class="brand-name">KESTON FIELDWORKS</div>

    <div class="person">
      <div class="person__name">DEAN HARLOW</div>
      <div class="person__role">Director</div>
    </div>

    <ul class="contact">
      <li>
        <svg viewBox="0 0 10 10"><path d="M1 3.5C1 2 3 1 5 1s4 1 4 2.5L7.5 4.5 6.8 3.4H3.2L2.5 4.5zM2.5 5h5l1 4h-7z"/></svg>
        0487305526
      </li>
      <li>
        <svg viewBox="0 0 10 10"><path d="M0 2h10v6H0zm1 1v.3l4 2.5 4-2.5V3z"/></svg>
        dean@kolvat.biz
      </li>
      <li>
        <svg viewBox="0 0 10 10"><circle cx="5" cy="5" r="4.3" fill="none" stroke="#2f4a8a" stroke-width="1"/><path d="M0.7 5h8.6M5 0.7v8.6" stroke="#2f4a8a" stroke-width="0.8"/><ellipse cx="5" cy="5" rx="2" ry="4.3" fill="none" stroke="#2f4a8a" stroke-width="0.8"/></svg>
        www.kestonfieldworks.com
      </li>
    </ul>

    <div class="social" aria-label="Social profiles"><span></span><span></span><span></span></div>

    <div class="strip"></div>
    <div class="band">www.kolvat.biz</div>
  </section>

</main>
</body>
</html>
```